New Business Card Design for Manufacturing

We are an engineering/manufacturing company that offers Advanced machining/assembly/engineering services, as well as innovative products for the heavy duty engine cooling markets.

We are looking to get a new business card designed that is clean and modern looking, but still fits the wide range of technical/skilled work we do.

- We hope to use this design as the base for other design work in new Presentations, web, and print work.

Industry/Entity Type

Engineering

Contact Information for Business Card

Our preferred color of blue is (RGB) 22/71/159 but can vary slightly from that color. Our content will be our Logo and full company name (Vantrell Forge Works, Inc.), company address, name, job title, phone number with extension, cell number, fax number, website, and email address on the cards.
We'd like the full company name next to the logo, but we are open to other interpretations of that layout.
Preferably, we would like the back side to be clean with just our logo, and the front to contain all of the contact information.

Colors
2f74b4
0355a3
85abd2

Requirements
Must have
• - Logo, company name, needed content - We are open to interpretation beyond that.
• - Standard size business card.
• - Horizontal orientation.
• - Enough space for lengthy names / job titles (for example, a job title could read "Directory of Human Resources" or "V.P. of Governmental Affairs"). We need this to look clean, whether the title be short (CEO) or long (as described above).

```html
<!DOCTYPE html>
<html lang="en">
<head>
<meta charset="utf-8">
<title>Vantrell Forge Works — Business Card</title>
<link rel="stylesheet" href="https://fonts.googleapis.com/css2?family=Roboto:wght@400;700&family=Roboto+Condensed:wght@500&display=swap">
<style>
  :root {
    --page-bg: #ecebe8;
    --brand-blue: #1150a0;
    --card-white: #f7f7f7;
    --card-grey: #7b8186;
    --tagline-grey: #8a8f94;
    --ink-white: #ffffff;
  }
  * { margin: 0; padding: 0; box-sizing: border-box; }
  html, body { width: 1200px; height: 960px; overflow: hidden; }
  body {
    position: relative;
    background: var(--page-bg);
    font-family: "Roboto", Arial, sans-serif;
  }
  .card {
    position: absolute;
    width: 600px;
    height: 343px;
    border-radius: 22px;
    overflow: hidden;
    box-shadow: 0 3px 8px rgba(0,0,0,0.25);
  }
  .card-front { left: 302px; top: 128px; background: var(--card-white); }
  .card-back { left: 298px; top: 488px; background: var(--card-grey); }

  .front-band {
    position: absolute;
    left: 0; top: 0;
    width: 600px; height: 343px;
  }

  .brand-lockup {
    position: absolute;
    left: 52px; top: 60px;
  }
  .brand-name {
    font-weight: 700;
    font-size: 30px;
    line-height: 1.05;
    color: var(--brand-blue);
    text-transform: uppercase;
    letter-spacing: 0.5px;
  }
  .brand-tagline {
    margin-top: 10px;
    font-weight: 700;
    font-size: 13px;
    color: var(--tagline-grey);
    text-transform: uppercase;
    letter-spacing: 0.3px;
  }

  .contact-block {
    position: absolute;
    left: 52px; top: 212px;
    color: var(--ink-white);
    font-size: 14px;
    line-height: 19px;
  }
  .contact-address { margin-bottom: 10px; }
  .contact-line { display: flex; align-items: center; gap: 7px; }
  .contact-line svg { width: 13px; height: 13px; fill: var(--ink-white); flex: none; }

  .person {
    position: absolute;
    right: 49px; top: 262px;
    text-align: right;
    color: var(--ink-white);
  }
  .person-name {
    font-family: "Roboto Condensed", "Arial Narrow", sans-serif;
    font-weight: 500;
    font-size: 26px;
    line-height: 30px;
    text-transform: uppercase;
  }
  .person-title { font-size: 14px; line-height: 18px; }

  .back-lockup {
    position: absolute;
    left: 0; right: 0; top: 120px;
    text-align: center;
    color: var(--ink-white);
  }
  .back-name {
    font-weight: 700;
    font-size: 40px;
    line-height: 1.1;
    text-transform: uppercase;
  }
  .back-tagline {
    margin-top: 12px;
    font-weight: 700;
    font-size: 18px;
    text-transform: uppercase;
    letter-spacing: 0.4px;
  }
  .back-website {
    position: absolute;
    left: 0; right: 0; top: 284px;
    text-align: center;
    color: var(--ink-white);
    font-size: 13px;
    letter-spacing: 2.2px;
  }
</style>
</head>
<body>

<section class="card card-front">
  <svg class="front-band" viewBox="0 0 600 343" aria-hidden="true">
    <path d="M0 183 H488 L510 221 L510 183 H600 V343 H0 Z" fill="var(--brand-blue)"/>
  </svg>

  <div class="brand-lockup">
    <div class="brand-name">Vantrell Forge Works, Inc.</div>
    <div class="brand-tagline">Built to Endure</div>
  </div>

  <div class="contact-block">
    <div class="contact-address">4120 Copperfield Road<br>Ridgemont, Alaska 99612</div>
    <div class="contact-line">
      <svg viewBox="0 0 24 24"><path d="M6.6 10.8a15.1 15.1 0 0 0 6.6 6.6l2.2-2.2c.3-.3.7-.4 1-.2 1.1.4 2.3.6 3.6.6.6 0 1 .4 1 1V20c0 .6-.4 1-1 1A17 17 0 0 1 3 4c0-.6.4-1 1-1h3.5c.6 0 1 .4 1 1 0 1.3.2 2.5.6 3.6.1.3 0 .7-.2 1z"/></svg>
      <span>555 214 0387</span>
    </div>
    <div class="contact-line">
      <svg viewBox="0 0 24 24"><path d="M7 1h10a2 2 0 0 1 2 2v18a2 2 0 0 1-2 2H7a2 2 0 0 1-2-2V3a2 2 0 0 1 2-2zm0 3v14h10V4zm5 15.5a1 1 0 1 0 0 2 1 1 0 0 0 0-2z"/></svg>
      <span>555 730 6142</span>
    </div>
    <div class="contact-line">
      <svg viewBox="0 0 24 24"><path d="M2 5h20v14H2zm2 2v.5l8 5 8-5V7zm0 2.9V17h16V9.9l-8 5z"/></svg>
      <span>dorian@vantrellforge.com</span>
    </div>
  </div>

  <div class="person">
    <div class="person-name">Dorian Pell</div>
    <div class="person-title">V.P. of Governmental Affairs</div>
  </div>
</section>

<section class="card card-back">
  <div class="back-lockup">
    <div class="back-name">Vantrell Forge Works</div>
    <div class="back-tagline">Built to Endure</div>
  </div>
  <div class="back-website">www.vantrellforgeworks.com</div>
</section>

</body>
</html>
```